Web site for a company that sells Pinball machines

We need a website that is an online shopping experience for a Store that sells pinball machines and accessories. The name of the store is called "Gadget Arcade." The store it self has a showroom, but we would also like to have an Internet e-commerce presence. We pinball machines made by Vexler pinball. You can visit their website and see their current list of machines as well as their website for the machines that we are going to carry in our store. Their website is Vexlerpinball.com. I am able to use their machine photos as well as their machine brochure PDF files. I am also able to use their logo on my website two list it as a Vexler Authorized Dealer.
This website design needs to be funky, fun, very technologically oriented and modern. The people buying machines our spending anywhere between $5000 and $15,000 on one machine. These Are high-end buyers who are also usually fairly tech savvy or at least enjoy technology and graphics.
Attachments: I have attached photographs of some of my own machines which may be used in the website. I've also attached some downloaded files from Vexler pinball.com as well as some of their PDF files for brochures. I will carry all of their current models they have listed under games. Not the archived games. I have included one of their machines called Thunderwolf Limited edition in my photograph attachments. The rest of the photos are just random pictures that I have taken myself and maybe used to build the site. Lastly I have attached my logo which I am not super crazy about so I will also be posting a contest to redesign this logo. Tons more of my own pinball photos are available.
I would like for people to be able to purchase machines and accessories from the website, but also inform them to our actual showroom.
Updates
Project Deadline Extended Reason: Hello. We have extended five days due to some complications during the construction of our actual building. We were unable to participate in this web design during this time and so unfortunately were not able give feedback appropriately. We are back on track and will provide feedback to the designers who have designed up until this point. We will still be interested in seeing new submissions, however; this extension will give us a chance to provide feedback and coordinate the website appropriately. Thank you so much for your submissions and your patience!!!!Gadget Arcade Added Friday, April 21, 2017
Target Market(s)
Target market is 16 to 75. Techy individuals to enjoy gaming technology video animation and Vegas style twinkle
Industry/Entity Type
It Company
Coding
Coded - Design and coding required
Number of Pages Required
3 page
Font styles to use
Look and feel
Each slider illustrates characteristics of the customer's brand and the style your logo design should communicate.

```html
<!DOCTYPE html>
<html lang="en">
<head>
<meta charset="utf-8">
<title>Gadget Arcade – Pinball Machines and Accessories</title>
<link rel="stylesheet" href="https://fonts.googleapis.com/css2?family=Montserrat:wght@400;500;600;700&family=Open+Sans:wght@400;600&display=swap">
<style>
:root{
  --ink:#2b2b2b;
  --muted:#8a8a8a;
  --line:#d6d6d6;
  --white:#ffffff;
  --accent:#c9302c;
  --paper:#f4f4f4;
  --night:#1a1526;
}
*{box-sizing:border-box;margin:0;padding:0}
html,body{width:1200px;height:3252px;overflow:hidden;background:var(--white)}
body{font-family:"Open Sans",Arial,sans-serif;color:var(--ink);position:relative}
.head{font-family:"Montserrat",Arial,sans-serif}
section,header,footer{position:absolute;left:0;width:1200px}

/* hero */
.hero{top:0;height:660px;overflow:hidden}
.hero-photo{position:absolute;inset:0;background:
  radial-gradient(circle at 18% 70%,#e0a53a 0,transparent 28%),
  radial-gradient(circle at 80% 60%,#b83b2c 0,transparent 30%),
  radial-gradient(circle at 55% 30%,#3d6fa8 0,transparent 35%),
  linear-gradient(160deg,#5a2d2a,#2a1f2e 60%,#6b3a1e)}
.hero-shade{position:absolute;inset:0;background:rgba(0,0,0,.28)}
.cart{position:absolute;top:36px;left:950px;display:flex;align-items:center;gap:10px;color:var(--white);font-size:14px}
.navbar{position:absolute;top:88px;left:140px;width:920px;height:48px;background:var(--white);display:flex;align-items:center;justify-content:space-between;padding:0 24px;box-shadow:0 2px 8px rgba(0,0,0,.3)}
.navbar ul{display:flex;list-style:none;gap:0}
.navbar li{font-family:"Montserrat",Arial,sans-serif;font-weight:600;font-size:14px;letter-spacing:.5px;padding:0 14px;border-right:1px solid var(--line)}
.navbar li:last-child{border-right:none}
.brand{position:absolute;top:20px;left:470px;width:260px;height:140px;background:var(--white);border-radius:0 0 60px 60px;display:flex;align-items:center;justify-content:center;gap:10px;box-shadow:0 2px 8px rgba(0,0,0,.3)}
.brand-dot{width:22px;height:22px;border-radius:50%;background:var(--accent)}
.brand-name{font-family:"Montserrat",Arial,sans-serif;font-weight:700;font-size:24px;color:var(--ink);letter-spacing:.5px}
.hero-title{position:absolute;top:300px;left:0;width:1200px;text-align:center;color:var(--white);font-weight:600;font-size:44px;line-height:54px;letter-spacing:2px;text-transform:uppercase}
.dots{position:absolute;top:626px;left:0;width:1200px;display:flex;justify-content:center;gap:12px}
.dots span{width:12px;height:12px;border-radius:50%;background:rgba(255,255,255,.5)}
.dots span.on{background:var(--white)}

/* about */
.about{top:660px;height:488px}
.about-text{position:absolute;left:120px;top:116px;width:580px}
.section-title{font-size:30px;font-weight:500;letter-spacing:1px;text-transform:uppercase;color:var(--muted)}
.section-title b{color:var(--ink);font-weight:600}
.about-text p{margin-top:22px;font-size:15px;line-height:26px;color:var(--muted)}
.btn{display:inline-block;margin-top:26px;padding:10px 22px;border:2px solid var(--ink);font-family:"Montserrat",Arial,sans-serif;font-weight:600;font-size:13px;letter-spacing:1px;text-transform:uppercase}
.machine{position:absolute;left:740px;top:52px;width:160px;height:400px;background:linear-gradient(180deg,#3c4f86,#1e2540 60%,#5b6ba3);border-radius:4px}

/* why */
.why{top:1148px;height:484px;overflow:hidden}
.why-photo{position:absolute;inset:0;background:
  radial-gradient(circle at 20% 40%,#4b5bc4 0,transparent 30%),
  radial-gradient(circle at 75% 65%,#a23c8a 0,transparent 32%),
  linear-gradient(120deg,#1c1838,#3b1f4f 50%,#141a30)}
.why-shade{position:absolute;inset:0;background:rgba(10,8,25,.45)}
.why svg{position:absolute;left:0;top:0}
.why-body{position:absolute;left:250px;top:86px;width:700px;text-align:center;color:var(--white)}
.why-body h2{font-size:32px;font-weight:600;letter-spacing:1px;text-transform:uppercase}
.rule{width:60px;height:3px;background:var(--white);margin:14px auto 18px}
.why-body p{font-size:15px;line-height:25px;margin-bottom:10px}
.why-body .btn{border-color:var(--white);margin-top:12px}

/* products */
.products{top:1632px;height:500px}
.products h2{position:absolute;top:42px;width:1200px;text-align:center;font-size:32px;font-weight:500}
.products .rule{position:absolute;top:94px;left:570px;margin:0;background:var(--ink)}
.cards{position:absolute;top:128px;left:120px;display:flex;gap:8px}
.card{width:234px;border:1px solid var(--line);text-align:center}
.card-photo{height:228px}
.card h3{font-size:16px;font-weight:600;margin-top:14px}
.card p{font-size:12px;color:var(--muted);margin:6px 0 16px}
.p1{background:linear-gradient(150deg,#2a4a8a,#b84a2a)}
.p2{background:linear-gradient(150deg,#1f6a7a,#d09a2a)}
.p3{background:linear-gradient(150deg,#6a2a6a,#d8b030)}
.p4{background:linear-gradient(150deg,#2a2a6a,#c03040)}

/* events */
.events{top:2132px;height:488px;overflow:hidden}
.events-photo{position:absolute;inset:0;background:
  radial-gradient(circle at 80% 25%,#c23a62 0,transparent 28%),
  radial-gradient(circle at 60% 75%,#d4a030 0,transparent 30%),
  linear-gradient(120deg,#3a2f5c,#5a2340 50%,#2a2240)}
.events svg{position:absolute;left:0;top:0}
.events-text{position:absolute;left:120px;top:96px;width:300px}
.events-text h2{font-size:28px;font-weight:500;text-transform:uppercase;letter-spacing:1px}
.events-text p{margin-top:18px;font-size:14px;line-height:24px;color:var(--muted)}

/* news */
.news{top:2620px;height:480px;overflow:hidden}
.news-photo{position:absolute;inset:0;background:
  radial-gradient(circle at 30% 50%,#5a6a7a 0,transparent 35%),
  linear-gradient(120deg,#1a1e24,#3a3f48 50%,#16181c)}
.news-shade{position:absolute;inset:0;background:rgba(0,0,0,.45)}
.news-body{position:absolute;top:90px;left:300px;width:600px;text-align:center;color:var(--white)}
.news-body h2{font-size:34px;font-weight:500;text-transform:uppercase;letter-spacing:1px}
.news-date{font-size:16px;margin-bottom:8px}
.news-body h3{font-size:24px;font-weight:400;line-height:32px;margin-bottom:14px}
.news-body p{font-size:14px;line-height:22px;color:#e0e0e0}
.arrow{position:absolute;top:282px}

/* footer */
.footer{top:3100px;height:152px;background:var(--white)}
.footer ul{position:absolute;left:120px;top:44px;display:flex;gap:28px;list-style:none}
.footer li{font-family:"Montserrat",Arial,sans-serif;font-weight:600;font-size:14px;text-transform:uppercase}
.copy{position:absolute;left:120px;top:80px;font-size:12px;color:var(--muted)}
.social{position:absolute;left:920px;top:40px;display:flex;gap:10px}
.social span{width:30px;height:30px;border-radius:50%;border:2px solid var(--ink)}
</style>
</head>
<body>

<header class="hero">
  <div class="hero-photo" role="img" aria-label="Close view of a lit pinball playfield with colourful targets"></div>
  <div class="hero-shade"></div>
  <div class="cart">
    <svg width="26" height="26" viewBox="0 0 26 26"><circle cx="13" cy="13" r="12" fill="none" stroke="#fff" stroke-width="1.5"/><path d="M7 9h2l2 7h7l1.5-5H10" fill="none" stroke="#fff" stroke-width="1.5"/><circle cx="12" cy="19" r="1" fill="#fff"/><circle cx="17" cy="19" r="1" fill="#fff"/></svg>
    <span>0 Items</span>
  </div>
  <nav class="navbar">
    <ul><li>About</li><li>Products</li><li>Community</li></ul>
    <ul><li>Support</li><li>Events</li><li>Contact</li></ul>
  </nav>
  <div class="brand"><span class="brand-dot"></span><span class="brand-name">Gadget Arcade</span></div>
  <h1 class="hero-title head">Gadget Arcade Pinball Machines<br>and Accessories</h1>
  <div class="dots"><span></span><span class="on"></span><span></span><span></span></div>
</header>

<section class="about">
  <div class="about-text">
    <h2 class="section-title head">About <b>Gadget Arcade</b></h2>
    <p>Our showroom brings the arcade home. We stock every current Vexler pinball title, tuned and tested by our own techs before delivery. Visit the floor to play before you buy, or order online with full setup included.</p>
    <span class="btn">Read more</span>
  </div>
  <div class="machine" role="img" aria-label="Upright pinball machine cabinet with backbox"></div>
</section>

<section class="why">
  <div class="why-photo" role="img" aria-label="Row of glowing pinball machines in a dark arcade"></div>
  <div class="why-shade"></div>
  <svg width="1200" height="484"><polygon points="190,70 1060,70 1010,392 140,392" fill="rgba(0,0,0,.15)" stroke="#fff" stroke-width="2"/></svg>
  <div class="why-body">
    <h2 class="head">Why our machine</h2>
    <div class="rule"></div>
    <p>Every machine is inspected, leveled and calibrated in our workshop. We handle delivery, install and care, so the first game feels perfect.</p>
    <p>Our team plays these tables daily and knows each ramp, toy and mode by heart.</p>
    <span class="btn">Read more</span>
  </div>
</section>

<section class="products">
  <h2 class="head">Our Products</h2>
  <div class="rule"></div>
  <div class="cards">
    <div class="card"><div class="card-photo p1" role="img" aria-label="Pinball playfield close-up"></div><h3 class="head">Product Name</h3><p>Short machine summary here</p></div>
    <div class="card"><div class="card-photo p2" role="img" aria-label="Pinball playfield close-up"></div><h3 class="head">Product Name</h3><p>Short machine summary here</p></div>
    <div class="card"><div class="card-photo p3" role="img" aria-label="Pinball playfield close-up"></div><h3 class="head">Product Name</h3><p>Short machine summary here</p></div>
    <div class="card"><div class="card-photo p4" role="img" aria-label="Pinball playfield close-up"></div><h3 class="head">Product Name</h3><p>Short machine summary here</p></div>
  </div>
</section>

<section class="events">
  <div class="events-photo" role="img" aria-label="Colourful pinball playfield with ramps and toys"></div>
  <svg width="1200" height="488"><polygon points="0,0 600,0 440,488 0,488" fill="rgba(244,244,244,.92)"/></svg>
  <div class="events-text">
    <h2 class="head">Our Events</h2>
    <p>Join our monthly tournament nights with prizes and new releases.</p>
    <p>League play every Thursday evening on the showroom floor. Free play launch parties for each new Vexler title.</p>
    <span class="btn">Read more</span>
  </div>
</section>

<section class="news">
  <div class="news-photo" role="img" aria-label="Pinball machine interior in low light"></div>
  <div class="news-shade"></div>
  <div class="news-body">
    <h2 class="head">Latest News</h2>
    <div class="rule"></div>
    <div class="news-date">24 Feb 2016</div>
    <h3>New Thunderwolf Limited edition tables arrive in the showroom</h3>
    <p>Three numbered cabinets are now on the floor for play. Reserve yours online or stop by this weekend to try one.</p>
  </div>
  <svg class="arrow" style="left:220px" width="20" height="36" viewBox="0 0 20 36"><path d="M17 3 3 18l14 15" fill="none" stroke="#fff" stroke-width="3"/></svg>
  <svg class="arrow" style="left:960px" width="20" height="36" viewBox="0 0 20 36"><path d="M3 3l14 15L3 33" fill="none" stroke="#fff" stroke-width="3"/></svg>
</section>

<footer class="footer">
  <ul><li>Home</li><li>About</li><li>Products</li><li>Community</li><li>Support</li><li>Events</li><li>Contact</li></ul>
  <div class="copy">© 2017 Gadget Arcade. All rights reserved. Terms of Use</div>
  <div class="social"><span></span><span></span><span></span><span></span></div>
</footer>

</body>
</html>
```